Business Cards used to invite people to our church

We are a church and have need of a business card sized advertisement that allows our members to hand them out in order to invite people to the church. I need the front of the card to say "You're Invited" or "Come Check us out". with the service times on the back of the card later.
I have attached one of the OLD cards we have used in the past, but we want a complete makeover, into a more modern style that does not require the image.
I am also replacing the old logo with a newer "flat" logo which is attached.
Please use marketing colors. (blue or red or something that catches attention)
Create a card that DOES NOT have the picture of the two people on the front
The information on the sample card back is correct to go onto new card
Target Market(s)
anyone
Industry/Entity Type
Business
Contact Information for Business Card
sertice times and address information which you can get from the sample card I uploaded. It should have "You're Invited" or "Come Check us out" on the front of the card with out logo.

```html
<!DOCTYPE html>
<html lang="en">
<head>
<meta charset="utf-8">
<title>Grace Harbor Ministries – Invitation Card</title>
<link rel="stylesheet" href="https://fonts.googleapis.com/css2?family=Open+Sans:wght@400;600;700&family=Pinyon+Script&display=swap">
<style>
  :root {
    --backdrop: #3b3532;
    --card-blue: #0096f8;
    --card-ink: #ffffff;
    --card-shadow: rgba(0, 0, 0, 0.45);
  }
  * { box-sizing: border-box; margin: 0; padding: 0; }
  html, body {
    width: 1200px;
    height: 844px;
    overflow: hidden;
    background: var(--backdrop);
  }
  .canvas {
    position: relative;
    width: 1200px;
    height: 844px;
    display: flex;
    align-items: center;
    justify-content: center;
    gap: 60px;
  }
  .card {
    width: 500px;
    height: 286px;
    background: var(--card-blue);
    color: var(--card-ink);
    box-shadow: 0 10px 28px var(--card-shadow);
    position: relative;
  }
  /* Front */
  .card-front .invite {
    position: absolute;
    left: 0;
    right: 0;
    top: 92px;
    text-align: center;
    font-family: "Pinyon Script", cursive;
    font-size: 72px;
    line-height: 1;
    font-weight: 400;
    word-spacing: 36px;
    padding-right: 30px;
  }
  /* Back */
  .card-back {
    font-family: "Open Sans", sans-serif;
    text-align: center;
    padding-top: 30px;
  }
  .ministry-name {
    display: flex;
    align-items: center;
    justify-content: center;
    gap: 10px;
    font-size: 19px;
    font-weight: 600;
    letter-spacing: 1.5px;
    text-transform: uppercase;
  }
  .ministry-name .mark {
    width: 16px;
    height: 16px;
    border-radius: 50%;
    background: var(--card-ink);
  }
  .contact {
    margin-top: 22px;
    font-size: 14px;
    font-weight: 700;
    line-height: 1.45;
  }
  .schedule {
    list-style: none;
    width: 300px;
    margin: 18px auto 0;
    font-size: 13px;
    line-height: 1.7;
  }
  .schedule li {
    display: flex;
    align-items: baseline;
  }
  .schedule .leader {
    flex: 1;
    border-bottom: 1px dotted var(--card-ink);
    margin: 0 4px;
    transform: translateY(-4px);
  }
</style>
</head>
<body>
  <main class="canvas">
    <section class="card card-front" aria-label="Card front">
      <p class="invite">You're Invited</p>
    </section>

    <section class="card card-back" aria-label="Card back">
      <h1 class="ministry-name"><span class="mark" aria-hidden="true"></span>Grace Harbor Ministries</h1>
      <p class="contact">
        2480. Cedar Lane - Riverton, Tx 75099<br>
        1-800-555-0142
      </p>
      <ul class="schedule">
        <li><span>Sunday</span><span class="leader"></span><span>9:00 Am</span></li>
        <li><span>Sunday</span><span class="leader"></span><span>11:00 Am</span></li>
        <li><span>Wed. Bible Class</span><span class="leader"></span><span>7:00 Pm</span></li>
      </ul>
    </section>
  </main>
</body>
</html>
```